New Business Card Design Project

I need a design for business cards, i am an electrical business called "Corvane Electrical and Communications" i need the cards to be double sided with the company logo on the back (attached) the front needs to say my company name, web site, email address, telephone number, and ABN number and electrical license number. I am open to different arrangements of the information but would like the background to be incorporating something electrical or something that looks smart. open to all additional ideas also.

The company colours are orange and grey see logo attached.

Business Name: Corvane Electrical and Communications
Website: corvaneelectricalandcomms.example.com.au
Email: brent@corvaneelectricalandcomms.example.com.au
Telephone(mobile): 0481209736
ABN: 71208349162
Lic No: 418273D

Target Market(s)

Business entities, Project Managers, Accounts, Clients

Industry/Entity Type

Electrician

Contact Information for Business Card

I need a design for business cards, i am an electrical business called "Corvane Electrical and Communications" i need the cards to be double sided with the company logo on the back (attached) the front needs to say my company name

Font styles to use
Serif
Sans Serif

Colors
f37122
5c5c5c

Requirements
Must have
• Must have the Logo on the back open to different ways of it being on the back but had in mind to keep it central but again open to other options
Nice to have
• A real modern cool background that is eye catching yet contemporary
Should not have
• No backgrounds of a light bulb or plug or anything like that

```html
<!DOCTYPE html>
<html lang="en">
<head>
<meta charset="utf-8">
<title>Corvane Electrical and Communications – Business Cards</title>
<link rel="stylesheet" href="https://fonts.googleapis.com/css2?family=Open+Sans:wght@400;600&display=swap">
<style>
  :root {
    --stage: #3a3a3a;
    --card-black: #050505;
    --white: #ffffff;
    --orange: #f7a823;
    --orange-deep: #f39a12;
    --grey: #5c5c5c;
    --light-text: #e6e6e6;
  }
  * { margin: 0; padding: 0; box-sizing: border-box; }
  html, body { width: 1200px; height: 900px; overflow: hidden; }
  body {
    background: var(--stage);
    font-family: "Open Sans", sans-serif;
    position: relative;
  }
  .card {
    position: absolute;
    width: 620px;
    height: 354px;
    border-radius: 22px;
    overflow: hidden;
    background: var(--card-black);
    box-shadow: 0 18px 40px rgba(0,0,0,0.45);
  }
  /* Logo side */
  .card--logo { left: 80px; top: 90px; }
  .logo-side__brand {
    position: absolute;
    left: 0; right: 0; top: 92px;
    text-align: center;
    color: var(--white);
    font-weight: 600;
  }
  .brand-mark {
    display: inline-block;
    width: 14px; height: 14px;
    border-radius: 50%;
    background: var(--orange);
    margin-right: 12px;
    vertical-align: middle;
  }
  .logo-side__name { font-size: 58px; letter-spacing: 3px; line-height: 1; vertical-align: middle; }
  .logo-side__sub { display: block; font-size: 17px; letter-spacing: 2px; margin-top: 12px; }
  .web-band {
    position: absolute;
    left: 0; right: 0; top: 252px; height: 52px;
    background: var(--white);
    display: flex; align-items: center; justify-content: center;
    font-size: 16px; color: var(--grey);
  }
  .web-band .accent { color: var(--orange); }

  /* Contact side */
  .card--contact { left: 500px; top: 466px; }
  .contact-side__art { position: absolute; inset: 0; }
  .contact-side__brand {
    position: absolute;
    left: 290px; top: 46px; width: 300px;
    text-align: center;
    color: var(--grey);
    font-weight: 600;
  }
  .contact-side__name { font-size: 40px; letter-spacing: 2px; line-height: 1; display: block; }
  .contact-side__sub { display: block; font-size: 12px; letter-spacing: 1.5px; margin-top: 8px; }
  .licence { display: block; font-size: 12px; font-weight: 400; margin-top: 8px; }
  .licence .accent { color: var(--orange); }
  .person {
    position: absolute; left: 30px; top: 178px; right: 30px;
  }
  .person__name {
    color: var(--orange); font-size: 24px; font-weight: 400; letter-spacing: 0.5px;
    display: flex; align-items: flex-end; gap: 12px;
  }
  .person__rule { flex: 1; height: 2px; background: var(--orange); margin-bottom: 8px; }
  .person__role { color: var(--light-text); font-size: 12px; letter-spacing: 0.5px; margin-top: 2px; }
  .details { position: absolute; left: 30px; top: 250px; color: var(--light-text); font-size: 14px; line-height: 1.45; }
  .details .label { color: var(--orange); font-weight: 600; }
  .details li { list-style: none; display: flex; align-items: center; gap: 10px; }
  .details svg { width: 12px; height: 12px; flex: none; }
  .details .abn { margin-bottom: 6px; }
</style>
</head>
<body>

<section class="card card--logo" aria-label="Business card logo side">
  <div class="logo-side__brand">
    <span class="brand-mark"></span><span class="logo-side__name">CORVANE</span>
    <span class="logo-side__sub">ELECTRICAL &amp; COMMUNICATIONS</span>
  </div>
  <div class="web-band">www.<span class="accent">corvaneelectricalandcomms</span>.example.com.au</div>
</section>

<section class="card card--contact" aria-label="Business card contact side">
  <svg class="contact-side__art" viewBox="0 0 620 354" aria-hidden="true">
    <path d="M205 0 C 250 150 430 222 620 200 L620 0 Z" fill="var(--orange-deep)"/>
    <path d="M232 0 C 280 140 440 205 620 193 L620 0 Z" fill="var(--white)"/>
  </svg>
  <div class="contact-side__brand">
    <span class="contact-side__name">CORVANE</span>
    <span class="contact-side__sub">ELECTRICAL &amp; COMMUNICATIONS</span>
    <span class="licence">Lic No: <span class="accent">418273D</span></span>
  </div>
  <div class="person">
    <div class="person__name">MARLO FENWICK <span class="person__rule"></span></div>
    <div class="person__role">DIRECTOR</div>
  </div>
  <ul class="details">
    <li class="abn"><span class="label">ABN:</span> 71208349162</li>
    <li>
      <svg viewBox="0 0 12 12"><path d="M2.5 1 L4.5 1 L5.2 3.6 L3.9 4.6 C4.6 6.1 5.9 7.4 7.4 8.1 L8.4 6.8 L11 7.5 L11 9.5 C11 10.3 10.3 11 9.5 11 C5 11 1 7 1 2.5 C1 1.7 1.7 1 2.5 1 Z" fill="var(--orange)"/></svg>
      0481-209-736
    </li>
    <li>
      <svg viewBox="0 0 12 12"><rect x="0.8" y="2.3" width="10.4" height="7.4" fill="none" stroke="var(--orange)" stroke-width="1.3"/><path d="M1 2.6 L6 6.6 L11 2.6" fill="none" stroke="var(--orange)" stroke-width="1.3"/></svg>
      brent@corvaneelectricalandcomms.example.com.au
    </li>
    <li>
      <svg viewBox="0 0 12 12"><circle cx="6" cy="6" r="5.2" fill="none" stroke="var(--orange)" stroke-width="1.2"/><ellipse cx="6" cy="6" rx="2.2" ry="5.2" fill="none" stroke="var(--orange)" stroke-width="1"/><line x1="0.8" y1="6" x2="11.2" y2="6" stroke="var(--orange)" stroke-width="1"/></svg>
      www.corvaneelectricalandcomms.example.com.au
    </li>
  </ul>
</section>

</body>
</html>
```